Web design for financial services

A modern web design of financial services (brokerage firm)
Req.s and technology tags :
- Very mobile friendly.
- One paged with some inner pages.
- Animated sticky header .
- Member login area for e-trade.
- Support RTL language.
- HTML & CSS.

The logo will be Home link
• MPTR :
WHO WE ARE
Content :
i) Board of Directors
ii) Mission Statement
iii) Corporate Values
iv) Regulations
• Financial Services :
WHAT WE DO
Content:
i) Electronic trading
ii) Trading desk
iii) Institutional
iv) Investors Education
• News
• Market Tools
• Forms---- opens new page
• Careers---- opens new page
• Contact Us----opens new page

The website is :
http://www.mptr-doha-example.com/

The logo need some changes to be more modern and impressively , but with keeping same structure .

Some related websites :
https://www.lv-bourse.example/

financial market

Financial Service

Coded - Design and coding required

2 page

• same fonts of http://www.kwdholdings.example/

• - Very mobile friendly.
• - One paged with some inner pages.
• - Animated sticky header .
• - Member login area for e-trade.
• - Support RTL language.
• - HTML & CSS.
• Slider , some Qatari theme,
• i like the video inside the home page
• ex :http://www.kwdholdings.example/

```html
<!DOCTYPE html>
<html lang="en">
<head>
<meta charset="utf-8">
<title>MPTR — Financial Services</title>
<link rel="stylesheet" href="https://fonts.googleapis.com/css2?family=Montserrat:wght@400;600;700;800&family=Open+Sans:wght@300;400;600&display=swap">
<style>
:root{
  --red:#8e1b1f;
  --ink:#222428;
  --text:#555a60;
  --muted:#8a8f95;
  --grey-band:#ececec;
  --footer:#2b2c30;
  --white:#ffffff;
}
*{box-sizing:border-box;margin:0;padding:0}
html,body{width:1200px;height:4304px;overflow:hidden}
body{font-family:"Open Sans",Arial,sans-serif;color:var(--text);background:var(--white);position:relative}
h1,h2,h3,h4,.nav,.btn{font-family:"Montserrat",Arial,sans-serif}
section,header,footer{position:absolute;left:0;width:1200px}

/* Hero */
.hero{top:0;height:640px;background:linear-gradient(180deg,#2a2f45 0%,#3b3550 40%,#2a2438 70%,#141622 100%);overflow:hidden}
.hero-photo{position:absolute;inset:0;background:linear-gradient(180deg,rgba(60,70,110,.5),rgba(90,60,90,.35) 55%,rgba(10,12,20,.8))}
.topbar{position:absolute;top:0;left:0;right:0;height:96px;background:rgba(10,12,20,.35)}
.logo{position:absolute;left:64px;top:30px;display:flex;align-items:center;gap:10px;color:var(--white);font:700 22px "Montserrat",sans-serif;letter-spacing:1px}
.logo i{width:14px;height:14px;border-radius:50%;background:var(--red);display:block}
.util{position:absolute;right:64px;top:16px;display:flex;gap:10px}
.btn-login{background:var(--red);color:var(--white);font:600 11px "Montserrat",sans-serif;padding:6px 14px}
.lang{border:1px solid rgba(255,255,255,.5);color:var(--white);font:400 11px "Open Sans",sans-serif;padding:5px 14px}
.nav{position:absolute;right:64px;top:58px;display:flex;gap:30px;color:var(--white);font-size:12px;font-weight:600;letter-spacing:.5px}
.play{position:absolute;left:570px;top:262px;width:60px;height:60px;border:2px solid rgba(255,255,255,.7);border-radius:50%}
.hero h1{position:absolute;top:340px;width:100%;text-align:center;color:var(--white);font-family:"Open Sans",sans-serif;font-weight:300;font-size:50px}
.hero .sub{position:absolute;top:402px;width:100%;text-align:center;color:#e6e6ee;font-weight:300;font-size:30px}

/* Who we are */
.who{top:640px;height:660px}
.who-photo{position:absolute;right:0;top:0;width:740px;height:660px;background:linear-gradient(135deg,#c9ccd2,#8f96a4 50%,#3a4256)}
.who-cut{position:absolute;left:0;top:0}
.who-text{position:absolute;left:100px;top:80px;width:400px}
.who h2{font-size:38px;font-weight:800;color:var(--ink);margin-bottom:30px}
.who h4{font-size:13px;font-weight:700;color:var(--ink);margin:22px 0 8px}
.who p{font-size:12px;line-height:1.75}
.btn{display:inline-block;background:var(--red);color:var(--white);font-size:11px;font-weight:700;padding:10px 20px;margin-top:30px}

/* Market index */
.index{top:1330px;height:270px;text-align:center}
.index h2{font-size:38px;font-weight:800;color:var(--ink);margin-top:50px}
.index p{width:760px;margin:24px auto 0;font-size:12px;line-height:1.7}

/* What we do */
.what{top:1600px;height:660px}
.what-photo{position:absolute;right:0;top:0;width:640px;height:660px;background:linear-gradient(135deg,#dcdde0,#a9adb3 50%,#3e4149)}
.what-text{position:absolute;left:100px;top:60px;width:440px}
.what h2{font-size:38px;font-weight:800;color:var(--ink)}
.what .lead{font-size:13px;font-weight:600;color:var(--ink);margin:26px 0 18px;line-height:1.6}
.what ul{list-style:none}
.what li{font-size:12px;line-height:2.1;padding-left:16px;position:relative}
.what li::before{content:"";position:absolute;left:0;top:11px;width:5px;height:5px;background:var(--red)}

/* Services */
.services{top:2300px;height:560px;text-align:center}
.services h2{font-size:38px;font-weight:800;color:var(--ink);margin-top:40px}
.services .lead{font-size:12px;margin-top:10px}
.service-row{display:flex;justify-content:center;gap:150px;margin-top:60px}
.service{width:210px}
.service h3{font-size:13px;font-weight:700;color:var(--ink);margin-top:22px;line-height:1.5}
.dots{display:flex;justify-content:center;gap:8px;margin-top:50px}
.dots span{width:8px;height:8px;border-radius:50%;background:#ccc}
.dots span:first-child{background:var(--red)}

/* News */
.news{top:2880px;height:380px}
.news h2{position:absolute;left:100px;top:20px;font-size:38px;font-weight:800;color:var(--ink)}
.arrows{position:absolute;right:100px;top:30px;display:flex;gap:4px}
.arrows span{width:26px;height:26px;border:1px solid #bbb;display:flex;align-items:center;justify-content:center}
.news-row{position:absolute;left:100px;top:100px;display:flex;gap:40px}
.news-item{width:220px}
.news-item h3{font-size:13px;font-weight:700;color:var(--ink);line-height:1.45}
.news-item .date{font-size:11px;color:var(--muted);margin:4px 0 12px}
.news-item .rule{width:60px;height:2px;background:var(--red);margin-bottom:14px}
.news-item p{font-size:12px;line-height:1.7}

/* Market tools */
.tools{top:3280px;height:680px;background:var(--grey-band)}
.tools h2{position:absolute;left:100px;top:50px;font-size:38px;font-weight:800;color:var(--ink)}
.tools-row{position:absolute;left:100px;top:140px;display:flex;gap:30px}
.tool{width:313px}
.tool-photo{height:250px}
.tool h3{font-size:14px;font-weight:700;color:var(--ink);margin:24px 0 10px}
.tool p{font-size:12px;line-height:1.7}

/* Partners */
.partners{top:3960px;height:184px;display:flex;align-items:center;justify-content:center;gap:70px}
.partners .chev{color:#999;font-size:20px}
.partner{width:100px;height:40px;background:#d4d6d9;border-radius:4px}

/* Footer */
.site-footer{top:4144px;height:160px;background:var(--footer);text-align:center}
.footer-logo{display:inline-flex;align-items:center;gap:8px;color:var(--white);font:700 20px "Montserrat",sans-serif;margin-top:22px;letter-spacing:1px}
.footer-logo i{width:12px;height:12px;border-radius:50%;background:var(--red);display:block}
.footer-nav{display:flex;justify-content:center;gap:48px;margin-top:18px;font:600 11px "Montserrat",sans-serif;color:#c9c9cc}
.copy{font-size:11px;color:#9a9a9e;margin-top:10px}
.social{display:flex;justify-content:center;gap:10px;margin-top:10px}
.social span{width:24px;height:24px;border-radius:50%;background:#55565b}
</style>
</head>
<body>

<header class="hero">
  <div class="hero-photo" role="img" aria-label="Night skyline of Doha towers with city lights"></div>
  <div class="topbar"></div>
  <div class="logo"><i></i>MPTR</div>
  <div class="util"><span class="btn-login">LOG IN</span><span class="lang">English ▾</span></div>
  <nav class="nav"><span>MPTR</span><span>FINANCIAL SERVICE</span><span>NEWS</span><span>MARKET TOOL</span><span>FORMS</span><span>CAREERS</span><span>CONTACT US</span></nav>
  <div class="play"><svg width="56" height="56" viewBox="0 0 56 56"><path d="M23 18 L39 28 L23 38 Z" fill="#fff" opacity=".85"/></svg></div>
  <h1>Marwa Pearl Trading</h1>
  <p class="sub">We are a financial services company</p>
</header>

<section class="who">
  <div class="who-photo" role="img" aria-label="Business team in suits in a meeting"></div>
  <svg class="who-cut" width="1200" height="660" viewBox="0 0 1200 660"><path d="M0 0 H660 L480 660 H0 Z" fill="#fff"/></svg>
  <div class="who-text">
    <h2>WHO WE ARE</h2>
    <p>Marwa Pearl Trading is a private Qatari company that aims to provide secure and technologically advanced methods of trading to its clients. These facilities enable clients to trade faster, more securely and privately, helping them put their strategy to use.</p>
    <h4>OUR VISION</h4>
    <p>We intend to optimise all company resources to position ourselves as a unique, competitive business model with the goal of generating highly competitive returns for our clients and shareholders, by providing accurate, rapid and reliable order execution, attractive financial products and services, sophisticated customer service by investing and implementing state-of-the-art technology, always in line with compliance to regulatory rules and regulations.</p>
    <span class="btn">ABOUT MPTR</span>
  </div>
</section>

<section class="index">
  <h2>MARKET INDEX</h2>
  <p>Marwa Pearl Trading is a private Qatari company that aims to provide secure and technologically advanced methods of trading to its clients. These facilities enable clients to trade faster, more securely and privately, helping them put their strategy to use, with the online portal we begin.</p>
</section>

<section class="what">
  <div class="what-photo" role="img" aria-label="Hands holding a tablet showing market charts"></div>
  <svg style="position:absolute;left:0;top:0" width="1200" height="660" viewBox="0 0 1200 660"><path d="M0 0 H620 L560 660 H0 Z" fill="#fff"/></svg>
  <div class="what-text">
    <h2>WHAT WE DO</h2>
    <p class="lead">Marwa Pearl Trading offers various trading &amp; investment services</p>
    <ul>
      <li>Trading Account Registration</li>
      <li>Electronic Registration</li>
      <li>Deposit &amp; Withdraw Stocks from &amp; to Central Depository</li>
      <li>Buy &amp; Sell Order Execution</li>
      <li>Live Market Data Feeds</li>
      <li>Periodical detailed reports concerning clients' portfolios and account statements</li>
      <li>Electronic Trade</li>
      <li>Financial Broker SMS</li>
      <li>Marketing Bulls — Coming Soon</li>
      <li>IPO Shares</li>
      <li>Mailing Trading Summary</li>
      <li>Call Center 24/7</li>
    </ul>
    <span class="btn">READ MORE</span>
  </div>
</section>

<section class="services">
  <h2>OUR SERVICES</h2>
  <p class="lead">Marwa Pearl Trading offers various trading &amp; investment services</p>
  <div class="service-row">
    <div class="service">
      <svg width="150" height="150" viewBox="0 0 150 150"><path d="M75 8 L133 41 L133 109 L75 142 L17 109 L17 41 Z" fill="none" stroke="#c4c4c4" stroke-width="10"/><path d="M75 8 L133 41 L133 109" fill="none" stroke="var(--red)" stroke-width="10"/><rect x="52" y="55" width="46" height="40" fill="none" stroke="var(--red)" stroke-width="3"/><path d="M58 88 V78 M68 88 V70 M78 88 V74 M88 88 V64" stroke="var(--red)" stroke-width="4"/></svg>
      <h3>TRADING ACCOUNT REGISTRATION SERVICES</h3>
    </div>
    <div class="service">
      <svg width="150" height="150" viewBox="0 0 150 150"><path d="M75 8 L133 41 L133 109 L75 142 L17 109 L17 41 Z" fill="none" stroke="#c4c4c4" stroke-width="10"/><path d="M17 109 L17 41 L75 8" fill="none" stroke="var(--red)" stroke-width="10"/><rect x="48" y="56" width="54" height="38" rx="3" fill="none" stroke="var(--red)" stroke-width="3"/><circle cx="63" cy="71" r="6" fill="var(--red)"/><path d="M76 68 H94 M76 76 H94 M56 85 H94" stroke="var(--red)" stroke-width="3"/></svg>
      <h3>ELECTRONIC REGISTRATION</h3>
    </div>
    <div class="service">
      <svg width="150" height="150" viewBox="0 0 150 150"><path d="M75 8 L133 41 L133 109 L75 142 L17 109 L17 41 Z" fill="none" stroke="#c4c4c4" stroke-width="10"/><path d="M133 109 L75 142 L17 109" fill="none" stroke="var(--red)" stroke-width="10"/><rect x="50" y="56" width="50" height="36" fill="none" stroke="var(--red)" stroke-width="3"/><path d="M57 66 H80 M57 74 H76" stroke="var(--red)" stroke-width="3"/><circle cx="88" cy="82" r="7" fill="var(--red)"/></svg>
      <h3>DEPOSIT &amp; WITHDRAW STOCKS FROM &amp; TO CENTRAL DEPOSITARY</h3>
    </div>
  </div>
  <div class="dots"><span></span><span></span><span></span></div>
</section>

<section class="news">
  <h2>IN THE NEWS</h2>
  <div class="arrows"><span><svg width="8" height="12" viewBox="0 0 8 12"><path d="M7 1 L2 6 L7 11" fill="none" stroke="#777" stroke-width="2"/></svg></span><span><svg width="8" height="12" viewBox="0 0 8 12"><path d="M1 1 L6 6 L1 11" fill="none" stroke="#777" stroke-width="2"/></svg></span></div>
  <div class="news-row">
    <article class="news-item"><h3>MARKET NEWS :<br>LUSAIL EXCHANGE</h3><p class="date">Published 12 April 2017</p><div class="rule"></div><p>Shares closed higher on the main index as banking stocks led gains through the session, with steady volume from local investors.<br>read more...</p></article>
    <article class="news-item"><h3>MARKET NEWS :<br>LUSAIL EXCHANGE</h3><p class="date">Published 11 April 2017</p><div class="rule"></div><p>Real estate and industrial sectors posted modest moves while traders awaited quarterly results from major listed firms.<br>read more...</p></article>
    <article class="news-item"><h3>MARKET NEWS :<br>LUSAIL EXCHANGE</h3><p class="date">Published 10 April 2017</p><div class="rule"></div><p>Foreign fund flows stayed positive for the week, supporting blue chip names and lifting overall market value.<br>read more...</p></article>
    <article class="news-item"><h3>MARKET NEWS :<br>LUSAIL EXCHANGE</h3><p class="date">Published 09 April 2017</p><div class="rule"></div><p>The index eased slightly in early trade before recovering on buying interest in telecom and insurance shares.<br>read more...</p></article>
  </div>
</section>

<section class="tools">
  <h2>MARKET TOOLS</h2>
  <div class="tools-row">
    <div class="tool"><div class="tool-photo" role="img" aria-label="City towers lit at night" style="background:linear-gradient(135deg,#1c2030,#4a3a3a 60%,#b07a3a)"></div><h3>MOST ACTIVE COMPANY</h3><p>Track the most traded listed companies of the day by volume and value, updated live through the session.</p></div>
    <div class="tool"><div class="tool-photo" role="img" aria-label="Business people reviewing documents" style="background:linear-gradient(135deg,#d7d9dd,#7c8593 60%,#2e3442)"></div><h3>TOP GAINER</h3><p>See which shares rose the most today, with price change, percentage move and traded volume in one view.</p></div>
    <div class="tool"><div class="tool-photo" role="img" aria-label="Desk with laptop, charts and coffee" style="background:linear-gradient(135deg,#efe6da,#b39a80 60%,#5a4a3e)"></div><h3>TOP LOSER</h3><p>Follow the shares that fell the most today, with price change, percentage move and traded volume listed.</p></div>
  </div>
</section>

<section class="partners">
  <span class="chev">‹</span>
  <div class="partner"></div><div class="partner"></div><div class="partner"></div><div class="partner"></div><div class="partner"></div><div class="partner"></div>
  <span class="chev">›</span>
</section>

<footer class="site-footer">
  <div class="footer-logo"><i></i>MPTR</div>
  <nav class="footer-nav"><span>MPTR</span><span>FINANCIAL SERVICE</span><span>NEWS</span><span>MARKET TOOL</span><span>FORMS</span><span>CAREERS</span><span>CONTACT US</span></nav>
  <p class="copy">© COPYRIGHT 2017 . MPTR . ALL RIGHTS RESERVED . DOHA QATAR</p>
  <div class="social"><span></span><span></span><span></span><span></span></div>
</footer>

</body>
</html>
```